Logo + Label Design (Men’s Grooming Brand & Product Packaging)

Design a logo and 2 oz pomade label for Brel, a modern men’s grooming brand focused on clean, high-quality, natural ingredients. The design should establish a bold, masculine, minimalist identity that can later extend to products like shaving gel and body wash.

Key Requirements

Create a primary logo for “Brel” and a core label for the 2 oz pomade jar (screw-top).

Use a clean, modern style — masculine, confident, and approachable (think Dorran’s, Velta, Northfield Kit).

Design for 1–2 color screen printing on solid jar colors (white, black, or navy).

Avoid gradients, foil, or embossing. Must work in black & white.

Provide: vector logo, mockup of the 2 oz jar, color palette (CMYK/RGB/HEX), and font specs.

Winning design may lead to future projects (body wash, shave gel, skincare lines).

Font styles to use
Other font styles liked:
• We like the fonts and design concept in the attached mockup.

Requirements
Should not have
• We want to avoid too much writing or busy designs. We want to avoid having graphics/illustrations embedded in the logo if they will cause the brand to look less classy or sophisticated. We also want the design to look simple and all-American (e.g. Hollister and Vane, Pine Ledger, The KIM, etc). We’d like to give a Pellham & Royce vibe that feels classy and high end.

```html
<!DOCTYPE html>
<html lang="en">
<head>
<meta charset="utf-8">
<title>Brel Hair Pomade Label</title>
<link rel="stylesheet" href="https://fonts.googleapis.com/css2?family=Playfair+Display:wght@400;700;800&family=Crimson+Text:wght@400;700&display=swap">
<style>
  :root {
    --bg: #e8e4e0;
    --jar-black: #0b0b0b;
    --ink-white: #f2f2f2;
    --ink-soft: #cfcfcf;
    --accent-blue: #2f86d6;
    --rule: #d9d9d9;
  }
  * { box-sizing: border-box; margin: 0; padding: 0; }
  html, body { width: 1200px; height: 1200px; overflow: hidden; background: var(--bg); }
  body { position: relative; font-family: "Crimson Text", serif; color: var(--ink-white); }

  /* Lid label */
  .lid-label {
    position: absolute; left: 320px; top: 60px;
    width: 560px; height: 560px; border-radius: 50%;
    background: var(--jar-black);
  }
  .lid-label .product-type {
    position: absolute; left: 118px; top: 280px;
    transform: translate(-50%, -50%) rotate(-90deg);
    font-family: "Crimson Text", serif; font-weight: 700; font-size: 26px; white-space: nowrap;
  }
  .lid-label .divider {
    position: absolute; left: 172px; top: 150px; width: 2px; height: 260px; background: var(--rule);
  }
  .lid-label .brand-name {
    position: absolute; left: 210px; top: 120px;
    font-family: "Playfair Display", serif; font-weight: 700; font-size: 120px; line-height: 1;
    letter-spacing: -2px; color: var(--ink-white);
  }
  .lid-label .finish {
    position: absolute; left: 214px; top: 272px;
    font-family: "Playfair Display", serif; font-weight: 800; font-size: 27px; line-height: 1.02; letter-spacing: 1px;
  }
  .lid-label .scent {
    position: absolute; left: 214px; top: 345px;
    font-family: "Playfair Display", serif; font-weight: 800; font-size: 28px; letter-spacing: 1.5px; color: var(--accent-blue);
  }
  .lid-label .weight {
    position: absolute; left: 214px; top: 408px; font-size: 22px; letter-spacing: 1px;
  }

  /* Side wrap label */
  .wrap-label {
    position: absolute; left: 50px; top: 700px; width: 1100px; height: 420px;
    background: var(--jar-black);
    display: grid; grid-template-columns: 340px 2px 340px 2px 230px 2px 184px;
    align-items: center; padding: 0 0 0 30px;
  }
  .wrap-label .rule { width: 2px; height: 330px; background: var(--rule); }
  .usage { padding-right: 26px; font-size: 17px; line-height: 1.35; text-align: justify; color: var(--ink-soft); }
  .usage p + p { margin-top: 40px; }
  .wrap-label .brand-name {
    text-align: center; font-family: "Playfair Display", serif; font-weight: 700;
    font-size: 150px; line-height: 1; letter-spacing: -3px; color: var(--ink-soft);
  }
  .wrap-details { position: relative; height: 330px; }
  .wrap-details .product-type {
    position: absolute; left: 22px; top: 170px; transform: translate(-50%, -50%) rotate(-90deg);
    font-weight: 700; font-size: 24px; white-space: nowrap;
  }
  .wrap-details .finish { position: absolute; left: 62px; top: 50px; font-size: 27px; line-height: 1.05; }
  .wrap-details .scent { position: absolute; left: 62px; top: 130px; font-size: 26px; color: var(--accent-blue); }
  .wrap-details .weight { position: absolute; left: 90px; top: 275px; font-size: 16px; letter-spacing: 1px; }
  .feature-box {
    margin-left: 20px; border: 1.5px solid var(--rule); border-radius: 8px;
    padding: 14px 12px; font-size: 15px; line-height: 1.5; list-style: none; width: 150px;
  }
  .feature-box li::before { content: "• "; }
</style>
</head>
<body>
  <section class="lid-label" aria-label="Jar lid label">
    <div class="product-type">Hair Pomade</div>
    <div class="divider"></div>
    <div class="brand-name">brel</div>
    <div class="finish">Matte Finish<br>Medium Hold</div>
    <div class="scent">Fresh &amp; Clean</div>
    <div class="weight">2 oz ( 57 g )</div>
  </section>

  <section class="wrap-label" aria-label="Jar side label">
    <div class="usage">
      <p>Directions: Rub a small amount of pomade between hands and apply to damp hair (for sleeker look) or dry hair (for a matte look). Caution: For external use only. Avoid contact with eyes. If irritation occurs, discontinue use.</p>
      <p>Ingredients: Butyrospermum Parkii (Shea Butter), Cera Alba (Beeswax), Cera Bellina, Caprylic/Capric Triglyceride, Cocos Nucifera (Coconut Oil), Tocopherol (Vitamin E), Fragrance.</p>
    </div>
    <div class="rule"></div>
    <div class="brand-name">brel</div>
    <div class="rule"></div>
    <div class="wrap-details">
      <div class="product-type">Hair Pomade</div>
      <div class="finish">Matte Finish<br>Medium Hold</div>
      <div class="scent">Fresh &amp; Clean</div>
      <div class="weight">2 oz ( 57 g )</div>
    </div>
    <div class="rule"></div>
    <ul class="feature-box">
      <li>Naturally derived</li>
      <li>For all hair types</li>
      <li>Made in USA</li>
      <li>No parabens</li>
      <li>Cruelty free</li>
    </ul>
  </section>
</body>
</html>
```